Electronics Recycling and IT Asset Disposition Flyer and Brochure Design

We need a 2 side A5 Flyer and 4 side A4 folder( brochure) for our electronics waste recycling and IT asset management and disposition business.
Our business provides free electronics waste recycling for companies, schools, learning institutions,councils, IT companies and government sectors. Many people are ignorant of responsible recycling of electronics which could harm our health if not treated properly.
The list of other services attached in the pdf.
We provide an end to end and tailored solution for our customers from collection, logistics, data sanitisation, remarketing and recycling.

The Flyer should create awareness of responsible electronics recycling and drive the audience to contact us or go to our website to learn more about the company and services.A brief list of services should also be included in the flyer.The goal is to get the audience to contact us to enquire more about our services.

The Brochure should include all the above plus provide more details about the company, processes, services,contact details (fb, linkedin,Twitter). The goal is to convert the audience to customers for recycling and provide other services as added services.

The final design for both flyer and brochure should communicate responsible recycling of electronic scrap and tailored solution for every organisation.

The company website is www.kelvane-scrap.com.au based in Australia. We serve clients nationwide.

Target Market(s)

IT companies, Corporate, schools and learning institutions, government sector

Industry/Entity Type

Recycling

Contact Information for Business Card

Name: Harold Pendrake
email: harold@kelvane-scrap.com.au
website: www.kelvane-scrap.com.au
mobile: +614 612 39057
Phone: 1300 46 2735

Font styles to use
Serif

Requirements
Must have
• I would like the designs to have more images and icons
Nice to have
Should not have
• none

```html
<!DOCTYPE html>
<html lang="en">
<head>
<meta charset="utf-8">
<title>Kelvane Scrap – Flyer</title>
<link href="https://fonts.googleapis.com/css2?family=Didact+Gothic&family=Quicksand:wght@500;700&family=Roboto+Condensed:wght@700&display=swap" rel="stylesheet">
<style>
:root{
  --green:#5aac3c;
  --green-mid:#2f9a48;
  --green-dark:#1e5a2a;
  --green-deep:#123d1c;
  --ink:#3a3a3a;
  --grey:#6f6f6f;
  --panel:#f1f1f1;
  --line:#d9d9d9;
  --backdrop:#ececec;
  --white:#ffffff;
}
*{margin:0;padding:0;box-sizing:border-box}
html,body{width:1200px;height:712px;overflow:hidden}
body{background:var(--backdrop);position:relative;font-family:"Didact Gothic",sans-serif;color:var(--ink)}
.page{position:absolute;background:var(--white)}
.page--front{left:57px;top:57px;width:513px;height:600px}
.page--back{left:625px;top:62px;width:515px;height:606px}
.top-rule{position:absolute;top:0;height:3px;background:var(--green)}

/* front */
.brand{position:absolute;left:0;right:0;top:10px;display:flex;justify-content:center;align-items:center;gap:7px;z-index:2}
.brand__mark{width:16px;height:16px;border-radius:50%;border:2px solid var(--green)}
.brand__name{font-family:"Didact Gothic",sans-serif;font-size:20px;color:var(--green)}
.hero-photo{position:absolute;left:0;top:45px;width:100%;height:156px;
  background:linear-gradient(135deg,#2f5a2c 0%,#4f8a3a 40%,#7fb54d 65%,#3a6a30 100%)}
.band-title{position:absolute;left:0;top:201px;width:100%;height:25px;background:var(--green);
  color:var(--white);font-family:"Quicksand",sans-serif;font-weight:700;font-size:19px;text-align:center;line-height:25px}
.about{position:absolute;left:0;top:226px;width:100%;height:137px;background:var(--panel);padding:12px 40px 0 40px}
.about p{font-size:6.8px;line-height:8.4px;color:var(--ink);margin-bottom:7px}
.slogan{position:absolute;left:68px;top:428px;font-family:"Roboto Condensed",sans-serif;font-weight:700;
  font-size:19px;line-height:22px;color:var(--green)}
.cycle{position:absolute;left:250px;top:367px;width:230px;height:230px}
.colour-bars{position:absolute;left:0;bottom:0;width:100%;height:9px;display:flex}
.colour-bars span{display:block;height:100%}

/* back */
.section-title{position:absolute;left:0;width:100%;text-align:center;font-family:"Quicksand",sans-serif;font-weight:700;color:var(--green)}
.icon-row{position:absolute;left:0;top:47px;width:100%;height:32px}
.service{position:absolute;left:50px;right:0;background:var(--panel)}
.service--plain{background:transparent}
.service__icon{position:absolute;left:14px;top:6px;width:28px;height:28px}
.service__body{position:absolute;left:77px;top:4px;right:14px}
.service__title{font-family:"Quicksand",sans-serif;font-weight:700;font-size:11px;color:var(--green);margin-bottom:2px}
.service__body p{font-size:6.6px;line-height:8px;color:var(--ink)}
.industries-icon{position:absolute;left:254px;top:403px;width:27px;height:27px}
.industries-text{position:absolute;left:123px;top:448px;width:335px;font-size:6.6px;line-height:8px}
.industries-lead{position:absolute;left:143px;top:489px;font-size:6.6px}
.industries-list{position:absolute;left:128px;top:504px;list-style:none}
.industries-list li{font-size:6.6px;line-height:8.1px;padding-left:15px;position:relative}
.industries-list li::before{content:"";position:absolute;left:0;top:2.5px;width:3.5px;height:3.5px;background:var(--green)}
.contact-bar{position:absolute;left:20px;right:20px;top:573px;border-top:1px solid var(--line);padding-top:5px;
  display:flex;justify-content:space-between;align-items:center;font-size:7px}
.contact-bar .item{display:flex;align-items:center;gap:5px}
</style>
</head>
<body>

<section class="page page--front">
  <div class="top-rule" style="left:208px;width:120px"></div>
  <div class="brand"><span class="brand__mark"></span><span class="brand__name">Kelvane Scrap</span></div>
  <div class="hero-photo" role="img" aria-label="Close-up photo of a green circuit board with chips and capacitors"></div>
  <h1 class="band-title">About Us</h1>
  <div class="about">
    <p>Kelvane Scrap is a full service IT asset disposition, electronics waste recycling and electronics scrap purchasing company in Australia. Our vision is to become an industry leader by building genuine relationships with clients based on integrity, service quality and consistency, as well as maximizing value recovery.</p>
    <p>Our focus is to reduce electronic waste generation through creating awareness in organisations and community about the importance of responsible recycling of electronics waste. Our goal is to provide end-to-end solution in e-waste management through established processes and technological innovations, drive higher returns for our customers and enhance conservation of raw metals within our ecosystem.</p>
    <p>Our team of dedicated engineers and professionals work with companies, government offices, institutions and SMEs across Australia to provide personalised IT asset disposal and e-waste management solutions to suit their needs. Our experience and knowledge in this industry will help us to understand and provide innovative solutions to manage your end of life IT assets. We aim at maximising returns and providing cost effective ways to ensure a positive impact on your bottom-line.</p>
  </div>

  <p class="slogan">“BE RESPONSIBLE<br>TODAY FOR A BETTER<br>FUTURE TOMORROW”</p>

  <svg class="cycle" viewBox="0 0 230 230" aria-label="E-waste recycling cycle: reuse, recover, recycle">
    <path d="M7,115 A108,108 0 0 1 169,21.5 L139,73.4 A48,48 0 0 0 67,115 Z" fill="#5aac3c" stroke="#fff" stroke-width="3"/>
    <path d="M169,21.5 A108,108 0 0 1 197.7,184.4 L151.8,145.9 A48,48 0 0 0 139,73.4 Z" fill="#fff" stroke="#d5d5d5" stroke-width="1.5"/>
    <path d="M197.7,184.4 A108,108 0 0 1 7,115 L67,115 A48,48 0 0 0 151.8,145.9 Z" fill="#6f6f6f" stroke="#fff" stroke-width="3"/>
    <circle cx="115" cy="117" r="46" fill="#e3e3e3"/>
    <circle cx="115" cy="115" r="44" fill="#fff"/>
    <text x="115" y="110" text-anchor="middle" font-family="Didact Gothic, sans-serif" font-size="12" fill="#222">E-waste</text>
    <text x="115" y="126" text-anchor="middle" font-family="Didact Gothic, sans-serif" font-size="12" fill="#222">Recycling</text>
    <g fill="none" stroke="#fff" stroke-width="1.6"><path d="M74,42 a6,6 0 1 1 2,8"/><path d="M72,38 l2,4 4,-2"/></g>
    <text x="92" y="49" font-family="Quicksand, sans-serif" font-weight="700" font-size="24" fill="#fff">01</text>
    <text x="28" y="60" font-family="Didact Gothic, sans-serif" font-size="7" fill="#fff">REUSE</text>
    <text font-family="Didact Gothic, sans-serif" font-size="3.6" fill="#fff">
      <tspan x="28" y="68">Reuse: each device is</tspan><tspan x="28" y="72.5">checked for its value</tspan><tspan x="28" y="77">and working units are</tspan><tspan x="28" y="81.5">readied for a second life.</tspan></text>
    <g stroke="#555" stroke-width="2" stroke-linecap="round"><path d="M158,37 l12,12"/><path d="M170,37 l-12,12"/></g>
    <text x="152" y="62" font-family="Didact Gothic, sans-serif" font-size="7" fill="#555">RECOVER</text>
    <text font-family="Didact Gothic, sans-serif" font-size="3.6" fill="#666">
      <tspan x="150" y="70">Recover: units that fail</tspan><tspan x="150" y="74.5">testing are stripped</tspan><tspan x="150" y="79">and their parts sorted.</tspan></text>
    <text x="160" y="140" font-family="Quicksand, sans-serif" font-weight="700" font-size="24" fill="#444">02</text>
    <text x="32" y="180" font-family="Quicksand, sans-serif" font-weight="700" font-size="24" fill="#fff">03</text>
    <text x="78" y="180" font-family="Didact Gothic, sans-serif" font-size="7" fill="#fff">RECYCLE</text>
    <text font-family="Didact Gothic, sans-serif" font-size="3.6" fill="#fff">
      <tspan x="78" y="188">Recycle: sorted metals and</tspan><tspan x="78" y="192.5">plastics go to partner</tspan><tspan x="78" y="197">refiners as raw material.</tspan></text>
    <g fill="none" stroke="#fff" stroke-width="1.4"><circle cx="148" cy="190" r="6"/><path d="M146,184 l3,0 -1,3"/></g>
  </svg>

  <div class="colour-bars">
    <span style="width:43px;background:var(--green)"></span>
    <span style="width:65px;background:var(--green-mid)"></span>
    <span style="width:78px;background:var(--green-dark)"></span>
    <span style="flex:1;background:var(--grey)"></span>
  </div>
</section>

<section class="page page--back">
  <div class="top-rule" style="left:0;width:100%;height:2px"></div>
  <h2 class="section-title" style="top:20px;font-size:19px">Service Offering</h2>

  <svg class="icon-row" viewBox="0 0 515 32" aria-hidden="true">
    <line x1="0" y1="15" x2="515" y2="15" stroke="#5aac3c" stroke-width="1.5"/>
    <g fill="#fff" stroke="#5aac3c" stroke-width="1.8">
      <circle cx="137" cy="15" r="14"/><circle cx="192" cy="15" r="14"/><circle cx="245" cy="15" r="14"/>
      <circle cx="294" cy="15" r="14"/><circle cx="344" cy="15" r="14"/><circle cx="394" cy="15" r="14"/>
    </g>
    <g fill="#5aac3c">
      <rect x="128" y="10" width="11" height="8"/><rect x="139" y="12" width="6" height="6"/>
      <rect x="186" y="7" width="11" height="15" fill="none" stroke="#5aac3c" stroke-width="1.3"/>
      <rect x="188" y="11" width="7" height="1.3"/><rect x="188" y="14" width="7" height="1.3"/><rect x="188" y="17" width="5" height="1.3"/>
    </g>
    <g stroke="#5aac3c" stroke-width="2.2" stroke-linecap="round"><path d="M239,9 l12,12"/><path d="M251,9 l-12,12"/></g>
    <g fill="none" stroke="#5aac3c" stroke-width="1.6">
      <circle cx="294" cy="15" r="6"/><circle cx="344" cy="15" r="6"/><path d="M342,9 l3,0 -1,3"/>
    </g>
    <circle cx="394" cy="15" r="6.5" fill="none" stroke="#5aac3c" stroke-width="1.6"/>
    <path d="M392,12 l5,3 -5,3 z" fill="#5aac3c"/>
  </svg>

  <div class="service" style="top:86px;height:57px">
    <svg class="service__icon" viewBox="0 0 28 28" aria-hidden="true"><circle cx="14" cy="14" r="13" fill="#fff" stroke="#5aac3c" stroke-width="1.6"/><rect x="7" y="10" width="9" height="7" fill="#5aac3c"/><rect x="16" y="12" width="5" height="5" fill="#5aac3c"/></svg>
    <div class="service__body"><h3 class="service__title">Secure E-Waste Collection Service</h3>
      <p>Kelvane Scrap collects electronic waste from schools, businesses, home users and government departments<br>Secure collection includes pick up of e-waste and transportation to our recycling facility in a<br>secured truck<br>Registration of assets and reporting</p></div>
  </div>
  <div class="service service--plain" style="top:148px;height:52px">
    <svg class="service__icon" viewBox="0 0 28 28" aria-hidden="true"><circle cx="14" cy="14" r="13" fill="#fff" stroke="#5aac3c" stroke-width="1.6"/><rect x="9" y="7" width="10" height="14" fill="none" stroke="#5aac3c" stroke-width="1.3"/><path d="M11,11h6M11,14h6M11,17h4" stroke="#5aac3c" stroke-width="1.2"/></svg>
    <div class="service__body"><h3 class="service__title">Certified Data Sanitisation Service</h3>
      <p>Registering your assets on our Asset Management System<br>Test, audit and verify specifications, condition and resale value Provide a detailed asset report<br>Cleaning and removal of company logos and asset tags</p></div>
  </div>
  <div class="service" style="top:205px;height:71px">
    <svg class="service__icon" viewBox="0 0 28 28" aria-hidden="true"><circle cx="14" cy="14" r="13" fill="#fff" stroke="#5aac3c" stroke-width="1.6"/><path d="M9,9l10,10M19,9l-10,10" stroke="#5aac3c" stroke-width="2.2" stroke-linecap="round"/></svg>
    <div class="service__body"><h3 class="service__title">Data Centre Relocation and Decommissioning</h3>
      <p>To provide secure data destruction:<br>X1 pass<br>X3 pass (Recommended, DoD standard)<br>X7 pass<br>Total destruction of HDDs by degaussing<br>Total physical destruction of any storage media by shredding</p></div>
  </div>
  <div class="service service--plain" style="top:280px;height:30px">
    <svg class="service__icon" viewBox="0 0 28 28" style="top:1px" aria-hidden="true"><circle cx="14" cy="14" r="13" fill="#fff" stroke="#5aac3c" stroke-width="1.6"/><circle cx="14" cy="14" r="6" fill="none" stroke="#5aac3c" stroke-width="1.6"/></svg>
    <div class="service__body"><h3 class="service__title">IT Asset Remarketing</h3>
      <p>Recover client's IT asset and mobile devices for valuation and remarketing</p></div>
  </div>
  <div class="service" style="top:315px;height:37px">
    <svg class="service__icon" viewBox="0 0 28 28" style="top:4px" aria-hidden="true"><circle cx="14" cy="14" r="13" fill="#fff" stroke="#5aac3c" stroke-width="1.6"/><circle cx="14" cy="14" r="6" fill="none" stroke="#5aac3c" stroke-width="1.6"/><path d="M12,8l3,0-1,3" fill="none" stroke="#5aac3c" stroke-width="1.4"/></svg>
    <div class="service__body"><h3 class="service__title">Ewaste Recycling</h3>
      <p>All assets with no market value will be processed as E-Waste and recycled with zero to landfill<br>in our ISO certified partner refinery overseas for metals recovery</p></div>
  </div>
  <div class="service service--plain" style="top:356px;height:46px">
    <svg class="service__icon" viewBox="0 0 28 28" style="top:2px" aria-hidden="true"><circle cx="14" cy="14" r="13" fill="#fff" stroke="#5aac3c" stroke-width="1.6"/><circle cx="14" cy="14" r="7" fill="none" stroke="#5aac3c" stroke-width="1.6"/><path d="M12,11l5,3-5,3z" fill="#5aac3c"/></svg>
    <div class="service__body"><h3 class="service__title">Logistics Solutions</h3>
      <p>Deployment, relocation and decommissioning of IT systems by professional Quorvelle and Tandrisk<br>certified engineers<br>Data Center decommissioning/racking/de-racking and relocation<br>IT Systems deployment and support for small and medium size business</p></div>
  </div>

  <svg class="industries-icon" viewBox="0 0 28 28" aria-hidden="true"><circle cx="14" cy="14" r="13" fill="#5aac3c"/><rect x="8" y="9" width="12" height="11" fill="none" stroke="#fff" stroke-width="1.4"/><path d="M11,13h6M11,16h6" stroke="#fff" stroke-width="1.2"/></svg>
  <h2 class="section-title" style="top:432px;font-size:13px">Industries Served</h2>
  <p class="industries-text">No matter how big or small your organisation is or how complex or simple your IT systems are, we listen to the needs of your organisation to deliver customized, cost-effective and scalable solution. We ensure data destruction and responsible recycling of your electronic assets are our utmost priority. Our dedicated team is ready to serve you.</p>
  <p class="industries-lead">Industries we serve:</p>
  <ul class="industries-list">
    <li>Corporate</li><li>ITAD Companies</li><li>Financial Institutions</li><li>Educational &amp; Learning Institutions</li>
    <li>Councils</li><li>Recycling companies</li><li>Government sector</li>
  </ul>

  <div class="contact-bar">
    <span class="item"><svg width="9" height="9" viewBox="0 0 10 10" aria-hidden="true"><circle cx="5" cy="5" r="4.5" fill="none" stroke="#5aac3c"/><path d="M3.3,3 q0,3 3.4,4" stroke="#5aac3c" stroke-width="1.2" fill="none"/></svg>1300 46 2735</span>
    <span class="item">18-22 Carrow Street, Marsden Park 2765 NSW</span>
    <span class="item"><svg width="9" height="9" viewBox="0 0 10 10" aria-hidden="true"><circle cx="5" cy="5" r="4.5" fill="none" stroke="#5aac3c"/><path d="M0.5,5h9M5,0.5v9" stroke="#5aac3c" stroke-width="0.8"/></svg>www.kelvane-scrap.com.au</span>
  </div>

  <div class="colour-bars">
    <span style="width:45px;background:var(--green)"></span>
    <span style="width:62px;background:var(--green-mid)"></span>
    <span style="width:63px;background:var(--green-dark)"></span>
    <span style="flex:1;background:var(--line)"></span>
  </div>
</section>

</body>
</html>
```